Zielgruppe
Ich biete farbtupferei, Glitzertattoos, Schwangerschaftsbemalung (Belly-Painting), Wunden schminken, Vermietung von einer Popcornmaschine.
Aufgabenstellung
Mein Anliegen betrifft hiermit die Gestaltung einer Website.
In Bezug auf die Website gibt es schon eine gekaufte Domain, welche lautet: frau-pinselmaus.de und kann über VERAX eingerichtet werden.
Auf dieser WEBSITE soll sich folgendes Menü befinden:
- Anfrage stellen/Angebot einholen mit zusätzlicher Frage 'Wie sind Sie auf mich aufmerksam geworden?'
Mit einem Feld für den Namen, E-Mail, Telefonnummer, Gewünschtes Datum.
Sowie die Frage 'Wie sind Sie auf mich aufmerksam geworden?' (zum Ankreuzen) Freunde, Empfehlung, Flyer, soziale medienoder sonstiges.
Gerne auch zum ankreuzen welche Leistung Sie möchten. farbtupferei, Glitzer Tattoos, Schwangerschaftsbemalung, oder Popcornmaschiene. (So brauchen haben es die Kunden einfacher nur anzukreuzen und ich sehe gleich worum es sich handelt.)
- eine Leistungsübersicht: farbtupferei, Glitzertattoos, Schwangerschaftsbemalung (Belly-Painting), Wunden schminken, Vermietung von einer Popcornmaschine
- meine Kontaktdaten
- Galerie (es kann eine Auswahl der angehängten Bilder sein)
!!! mein Wunsch wäre, dass sich die Figur von dem Logo in verschiedenen Positionen auf der Website an das Menü angepasst wiederfindet (wenn dies irgendwie machbar ist)
z.B. meine Figur (Logo) stehend am Rand oder liegend.....
- erwünscht ist auch eine Verknüpfung mit einem Findlaeintrag
- Hinweis auf Kontaktor und Lumoravue (bin gerade dabei ein öffentliches Profil dort zu erstellen)
!Wichtig wäre die nötige Einstellung, damit die Website sowohl in der mobilen Version als auch der PC-Version mit ALLEN oben genannten Informationen dargestellt wird!
Dankbar wäre ich noch für die Information, ob für mich laufende Kosten (monatlich oder jährlich) für die Website entstehen?
Mein Logo ist mir sehr wichtig und sollte gut sichtbar und erkennbar sein auch die Schriftart kann auf der Website aufgegriffen werden

```html
<!DOCTYPE html>
<html lang="de">
<head>
<meta charset="utf-8">
<title>Tupfenreich – farbtupferei &amp; Glitzer Tattoos</title>
<link rel="stylesheet" href="https://fonts.googleapis.com/css2?family=Cormorant+Garamond:wght@500;600&family=Crimson+Pro:ital,wght@0,400;0,500;0,600;1,500;1,600&family=Mrs+Saint+Delafield&display=swap">
<style>
:root{
  --teal:#1b9cab;
  --teal-light:#93d2dd;
  --teal-pale:#b5e0e7;
  --teal-dark:#1e5f6a;
  --ink:#235e69;
  --white:#ffffff;
}
*{margin:0;padding:0;box-sizing:border-box}
html,body{width:1200px;height:4952px;overflow:hidden;background:var(--white)}
body{position:relative;font-family:"Crimson Pro",Georgia,serif;color:var(--ink)}
.abs{position:absolute}
.ph{position:absolute}

/* hero */
.hero-photo{left:0;top:0;width:1200px;height:312px;
  background:linear-gradient(100deg,#5b3b2c 0%,#e8672a 28%,#f07c2e 55%,#d9622a 80%,#8a4a30 100%);
  clip-path:polygon(0 0,100% 0,100% 52%,50% 100%,0 58%)}
.brand{left:450px;top:336px;width:300px;text-align:center}
.brand-name{font-family:"Cormorant Garamond",serif;font-weight:600;font-size:46px;letter-spacing:1px;color:var(--teal);line-height:1}

/* section titles */
.title{position:absolute}
.title-big{font-family:"Cormorant Garamond",serif;font-weight:600;color:var(--teal-light);line-height:1;letter-spacing:2px;font-size:84px;white-space:nowrap}
.title-script{position:absolute;font-family:"Mrs Saint Delafield",cursive;color:var(--teal-dark);font-size:44px;white-space:nowrap;line-height:1}
.subhead{position:absolute;font-family:"Crimson Pro",serif;font-weight:600;font-size:22px;text-align:center;letter-spacing:.5px;line-height:1.3;color:var(--ink)}
.body-copy{position:absolute;font-size:13.5px;line-height:21px;text-align:justify;color:var(--ink)}
.button{position:absolute;background:var(--teal);color:var(--white);font-family:"Crimson Pro",serif;font-weight:600;font-size:24px;letter-spacing:1px;display:flex;align-items:center;justify-content:center}

/* hallo */
.hallo-frame{left:262px;top:529px;width:440px;height:317px;background:var(--teal-pale)}
.hallo-photo-main{left:235px;top:558px;width:434px;height:327px;background:linear-gradient(120deg,#4a3026,#9a6a50 45%,#e0c24a 80%,#3a3e6a)}
.hallo-photo-arm{left:71px;top:777px;width:279px;height:371px;background:linear-gradient(160deg,#d9a0a2,#c77d86 50%,#8f5770)}

/* social */
.social-photo{left:0;top:1317px;width:1200px;height:818px;background:linear-gradient(110deg,#2c2a2b,#5a4a48 40%,#3a3536 70%,#242223)}
.social-title{left:0;top:1590px;width:1200px;text-align:center;font-family:"Mrs Saint Delafield",cursive;font-size:128px;color:var(--white);line-height:1}
.social-text{left:360px;top:1772px;width:520px;text-align:center;font-weight:600;font-size:33px;line-height:1.05;color:var(--white)}
.social-connect{left:0;top:1890px;width:1200px;text-align:center;font-family:"Mrs Saint Delafield",cursive;font-size:64px;color:var(--white)}

/* popcorn */
.popcorn-photo{left:590px;top:2160px;width:610px;height:760px;
  background:radial-gradient(ellipse at 35% 30%,#e9c27a 0%,#d9a85c 25%,rgba(255,255,255,0) 55%),
             linear-gradient(150deg,rgba(255,255,255,0) 55%,#d62f33 70%,#f3f0ee 78%,#c9262b 88%,rgba(255,255,255,0) 95%)}

/* reviews */
.reviews-band{left:0;top:3042px;width:1200px;height:170px;background:var(--teal-light)}
.review-bar{position:absolute;width:24px;background:var(--teal-light)}
.review-card{position:absolute;background:var(--white);height:320px}
.review-photo{position:absolute;top:20px;left:20px;height:285px}
.stars{position:absolute;display:flex;gap:5px}
.stars svg{width:46px;height:44px}
.review-name{position:absolute;font-family:"Crimson Pro",serif;font-style:italic;font-weight:600;font-size:44px;color:var(--teal-dark);line-height:1}
.review-text{position:absolute;font-size:20px;line-height:33px;color:var(--teal-dark);white-space:nowrap;overflow:hidden}

/* kontakt */
.kontakt-band{left:0;top:3865px;width:1200px;height:548px;background:linear-gradient(100deg,#1d5561,#226a76 45%,#1b5c68 100%)}
.kontakt-band::after{content:"";position:absolute;left:0;right:0;bottom:0;height:48px;background:#143f47}
.kontakt-text{left:60px;top:4148px;width:480px;text-align:center;font-weight:600;font-size:29px;line-height:43px;color:var(--white)}
.form-box{left:592px;top:3967px;width:500px;height:341px;background:var(--teal-light)}
.field{position:absolute;left:27px;width:435px;height:70px;background:var(--white);font-family:"Crimson Pro",serif;font-size:23px;font-weight:500;color:var(--teal-dark);display:flex;align-items:flex-end;padding:0 0 6px 10px;letter-spacing:1px}
.form-send{position:absolute;left:106px;top:231px;width:279px;height:67px;background:var(--white);color:var(--teal-dark);font-size:26px;font-weight:500;letter-spacing:1px;display:flex;align-items:center;justify-content:center}

/* painting */
.painting-frame{left:150px;top:4461px;width:350px;height:491px;background:var(--teal-light)}
.painting-photo{left:96px;top:4509px;width:366px;height:443px;background:linear-gradient(160deg,#5a3b28,#c9a47a 35%,#2b2b2e 70%,#6f5a4a)}
</style>
</head>
<body>

<header>
  <div class="ph hero-photo" role="img" aria-label="Foto: Schminkfarben und Pinsel auf einem orangefarbenen Tisch"></div>
  <div class="abs brand">
    <div class="brand-name">Tupfenreich</div>
  </div>
</header>

<section class="hallo">
  <div class="ph hallo-frame"></div>
  <div class="ph hallo-photo-main" role="img" aria-label="Foto: Künstlerin malt einem Kind ein Motiv auf den Arm"></div>
  <div class="ph hallo-photo-arm" role="img" aria-label="Foto: Glitzer-Tattoo auf einem Oberarm"></div>
  <p class="body-copy" style="left:448px;top:908px;width:304px">Lorem ipsum dolor sit amet, consetetur sadipscing elitr, sed diam nonumy eirmod tempor invidunt ut labore et dolore magna aliquyam erat, sed diam voluptua. At vero eos et accusam et justo duo dolores et ea rebum. Stet clita kasd gubergren, no sea takimata sanctus est Lorem ipsum dolor sit amet. Lorem ipsum dolor sit amet. Lorem ipsum dolor sit amet, consetetur sadipscing elitr, sed diam nonumy eirmod tempor invidunt ut labore et dolore magna aliquyam erat, sed diam voluptua.</p>
  <div class="title" style="left:790px;top:528px">
    <div class="title-big">HALLO</div>
    <div class="title-script" style="left:4px;top:42px">ich bin Name</div>
  </div>
  <h2 class="subhead" style="left:780px;top:646px;width:310px">LOREM IPSUM DOLOR SIT<br>AMET, CONSETETUR</h2>
  <p class="body-copy" style="left:788px;top:719px;width:304px">Lorem ipsum dolor sit amet, consetetur sadipscing elitr, sed diam nonumy eirmod tempor invidunt ut labore et dolore magna aliquyam erat, sed diam voluptua. At vero eos et accusam et justo duo dolores et ea rebum. Stet clita kasd gubergren, no sea takimata sanctus est Lorem ipsum dolor sit amet. Lorem ipsum dolor sit amet, consetetur sadipscing elitr, sed diam nonumy eirmod tempor invidunt ut labore et dolore magna aliquyam erat, sed diam voluptua. At vero eos et accusam et justo duo dolores et ea rebum. Stet clita kasd gubergren, no sea takimata sanctus est Lorem ipsum dolor sit amet.</p>
  <div class="button" style="left:813px;top:1056px;width:252px;height:56px">ENTDECKE MEHR</div>
</section>

<section class="social">
  <div class="ph social-photo" role="img" aria-label="Foto: Frau wird beim Schminken im Gesicht bemalt"></div>
  <svg class="abs" style="left:0;top:1221px" width="1200" height="180" viewBox="0 0 1200 180" aria-hidden="true">
    <path d="M0 0 C200 40 330 70 520 60 C760 45 930 70 1200 30 L1200 110 C1000 130 820 110 620 120 C400 135 200 110 0 96 Z" fill="#b5e0e7"/>
    <path d="M0 96 C220 112 400 140 620 126 C820 114 1000 132 1200 112 L1200 150 C980 170 780 150 560 165 C360 178 180 150 0 140 Z" fill="#93d2dd"/>
    <path d="M0 140 C180 152 360 180 560 168 C780 154 980 172 1200 150 L1200 180 L0 180 Z" fill="#6fbfcd" opacity=".6"/>
  </svg>
  <svg class="abs" style="left:0;top:2020px" width="1200" height="172" viewBox="0 0 1200 172" aria-hidden="true">
    <path d="M0 60 C220 20 420 40 620 50 C820 60 1000 10 1200 20 L1200 172 L0 172 Z" fill="#6fbfcd" opacity=".6"/>
    <path d="M0 80 C240 40 430 70 640 80 C860 92 1020 48 1200 40 L1200 130 C980 150 800 140 560 150 C340 160 180 170 0 160 Z" fill="#93d2dd"/>
    <path d="M0 160 C200 150 380 150 580 146 C820 140 1000 152 1200 130 L1200 172 L0 172 Z" fill="#ffffff"/>
  </svg>
  <div class="abs social-title">Social Media</div>
  <p class="abs social-text">Entdecke alle meine Leistungen Bilder und wirf einen Blick auf meine Arbeit!</p>
  <div class="abs social-connect">Let's Connect!</div>
</section>

<section class="popcorn">
  <div class="ph popcorn-photo" role="img" aria-label="Foto: Popcorn fliegt aus einem rot-weiß gestreiften Becher"></div>
  <div class="title" style="left:81px;top:2352px">
    <div class="title-big">POPCORN</div>
    <div class="title-script" style="left:14px;top:40px">auch das biete ich</div>
  </div>
  <h2 class="subhead" style="left:120px;top:2467px;width:340px">LOREM IPSUM DOLOR SIT<br>AMET, CONSETETUR</h2>
  <p class="body-copy" style="left:137px;top:2532px;width:304px">Lorem ipsum dolor sit amet, consetetur sadipscing elitr, sed diam nonumy eirmod tempor invidunt ut labore et dolore magna aliquyam erat, sed diam voluptua. At vero eos et accusam et justo duo dolores et ea rebum. Stet clita kasd gubergren, no sea takimata sanctus est Lorem ipsum dolor sit amet. Lorem ipsum dolor sit amet, consetetur sadipscing elitr, sed diam nonumy eirmod tempor invidunt ut labore et dolore magna aliquyam erat, sed diam voluptua. At vero eos et accusam et justo duo dolores et ea rebum. Stet clita kasd gubergren, no sea takimata sanctus est Lorem ipsum dolor sit amet.</p>
  <div class="button" style="left:163px;top:2865px;width:254px;height:58px">ENTDECKE MEHR</div>
</section>

<section class="reviews">
  <div class="ph reviews-band"></div>
  <div class="title" style="left:750px;top:3060px">
    <div class="title-big" style="color:#c6e8ee">REVIEWS</div>
    <div class="title-script" style="left:4px;top:40px;font-size:40px">mehr über meine arbeit</div>
  </div>

  <div class="review-bar" style="left:446px;top:3173px;height:190px"></div>
  <div class="review-bar" style="left:861px;top:3173px;height:190px"></div>

  <div class="review-card" style="left:62px;top:3173px;width:384px">
    <div class="ph review-photo" style="width:346px;background:linear-gradient(180deg,#ececec,#d7d7d7 55%,#b9b9b9)" role="img" aria-label="Foto: lächelnder Mann im grauen T-Shirt"></div>
  </div>
  <div class="review-card" style="left:477px;top:3173px;width:384px">
    <div class="ph review-photo" style="width:346px;background:linear-gradient(180deg,#e8ecef,#c9a07a 50%,#2a3a5a)" role="img" aria-label="Foto: Frau mit Brille und rotblondem Haar"></div>
  </div>
  <div class="review-card" style="left:888px;top:3173px;width:312px">
    <div class="ph review-photo" style="width:292px;background:linear-gradient(160deg,#f3d7a0,#e79ac0 45%,#8ec7e3 80%)" role="img" aria-label="Foto: Kind mit bunt geschminktem Schmetterlingsgesicht"></div>
  </div>

  <svg width="0" height="0" style="position:absolute" aria-hidden="true">
    <defs><symbol id="star" viewBox="0 0 24 23"><path d="M12 1.5l3 6.6 7.2.8-5.4 4.9 1.5 7.1L12 17.3l-6.3 3.6 1.5-7.1L1.8 8.9 9 8.1z" fill="#d6eff3" stroke="#5fb9c8" stroke-width="1.6" stroke-linejoin="round"/></symbol></defs>
  </svg>
  <div class="stars" style="left:80px;top:3485px"><svg><use href="#star"/></svg><svg><use href="#star"/></svg><svg><use href="#star"/></svg><svg><use href="#star"/></svg><svg><use href="#star"/></svg></div>
  <div class="stars" style="left:492px;top:3481px"><svg><use href="#star"/></svg><svg><use href="#star"/></svg><svg><use href="#star"/></svg><svg><use href="#star"/></svg><svg><use href="#star"/></svg></div>
  <div class="stars" style="left:904px;top:3481px"><svg><use href="#star"/></svg><svg><use href="#star"/></svg><svg><use href="#star"/></svg><svg><use href="#star"/></svg><svg><use href="#star"/></svg></div>

  <div class="review-name" style="left:64px;top:3555px">Lorem ipsum</div>
  <div class="review-name" style="left:490px;top:3548px">Lorem ipsum</div>
  <div class="review-name" style="left:910px;top:3548px">Lorem ipsum</div>

  <p class="review-text" style="left:64px;top:3598px;width:410px">sit amet, consetetur sadipscing elitr, sed<br>diam nonumy eirmod tempor invidunt ut<br>labore et dolore magna aliquyam erat, sed<br>diam voluptua.</p>
  <p class="review-text" style="left:490px;top:3591px;width:410px">sit amet, consetetur sadipscing elitr, sed<br>diam nonumy eirmod tempor invidunt ut<br>labore et dolore magna aliquyam erat, sed<br>diam voluptua.</p>
  <p class="review-text" style="left:910px;top:3591px;width:290px">sit amet, consetetur sadipscing elitr, sed<br>diam nonumy eirmod tempor invidunt ut<br>labore et dolore magna aliquyam erat, sed<br>diam voluptua.</p>
</section>

<section class="kontakt">
  <div class="ph kontakt-band" role="img" aria-label="Gedämpftes Foto: Schminkutensilien im Hintergrund"></div>
  <div class="title" style="left:96px;top:4015px">
    <div class="title-big" style="color:#4f9aa6">KONTAKT</div>
    <div class="title-script" style="left:14px;top:40px;color:#ffffff;font-size:40px">ruf mich doch mal an</div>
  </div>
  <p class="abs kontakt-text">Entdecke kommende Events oder<br>buche mich für dein Projekt</p>
  <form class="abs form-box" aria-label="Anfrage">
    <div class="field" style="top:43px">NAME</div>
    <div class="field" style="top:125px">EMAIL</div>
    <div class="form-send">ABSENDEN</div>
  </form>
</section>

<section class="painting">
  <div class="ph painting-frame"></div>
  <div class="ph painting-photo" role="img" aria-label="Foto: Schwangere mit Sonnenhut und bemaltem Babybauch"></div>
  <div class="title" style="left:686px;top:4520px">
    <div class="title-big" style="color:#a9dbe4">PAINTING</div>
    <div class="title-script" style="left:28px;top:40px;font-size:40px">babybauch painting</div>
  </div>
  <h2 class="subhead" style="left:700px;top:4647px;width:340px">LOREM IPSUM DOLOR SIT<br>AMET, CONSETETUR</h2>
  <p class="body-copy" style="left:731px;top:4705px;width:304px">Lorem ipsum dolor sit amet, consetetur sadipscing elitr, sed diam nonumy eirmod tempor invidunt ut labore et dolore magna aliquyam erat, sed diam voluptua. At vero eos et accusam et justo duo dolores et ea rebum. Stet clita kasd gubergren, no sea takimata sanctus est Lorem ipsum dolor sit amet. Lorem ipsum dolor sit amet. Lorem ipsum dolor sit amet, consetetur sadipscing elitr, sed diam nonumy eirmod tempor invidunt ut labore et dolore magna aliquyam erat, sed diam voluptua. At vero eos et accusam et justo duo dolores et ea rebum.</p>
</section>

</body>
</html>
```